Zolvana Stationary and Branding Documents

Corporate Identity Branding stationary needed for IT Recruiting Firm.

I already have a Logo, business cards and website. I need to get designs completed for the remaining corporate identity documents.

The documentation should use similar colors as my website and business card. The designs should modern and clean.

http://zolvanaworks.example/

Target Market(s)

Information Technology Industry

Industry/Entity Type

Information Technology

Colors
3377b5
0255a3
fbee3e
f78f20
f37122
33a6d7
000000
0592cd

Requirements
Must have
• Letter Head
• Folder Design
• PowerPoint Design
• Invoice
• Envelope
Nice to have
• Proposal
• Flyer
• Brochure
Should not have
• Logo
• Business Cards
• Website

```html
<!DOCTYPE html>
<html lang="en">
<head>
<meta charset="utf-8">
<title>Zolvana Letterhead</title>
<link href="https://fonts.googleapis.com/css2?family=Open+Sans:wght@400;600&display=swap" rel="stylesheet">
<style>
  :root {
    --backdrop: #dfe5f4;
    --paper: #f7f8f9;
    --brand-blue: #0255a3;
    --brand-orange: #f37122;
    --tile-1: #f7ede2;
    --tile-2: #f5ece3;
    --tile-3: #eeeae5;
    --footer-peach: #f5e4d5;
    --footer-blue: #d3e1ec;
    --footer-text: #555a60;
  }
  html, body {
    margin: 0;
    padding: 0;
    width: 1200px;
    height: 784px;
    overflow: hidden;
    background: var(--backdrop);
    font-family: "Open Sans", Arial, sans-serif;
  }
  .letterhead {
    position: absolute;
    left: 330px;
    top: 10px;
    width: 540px;
    height: 764px;
    background: var(--paper);
    box-shadow: 0 2px 10px rgba(40, 60, 120, 0.18);
    overflow: hidden;
  }
  .corner-tick {
    position: absolute;
    top: 14px;
    height: 4px;
    display: flex;
  }
  .corner-tick span { display: block; width: 16px; height: 4px; }
  .corner-tick .tick-blue { background: var(--brand-blue); }
  .corner-tick .tick-orange { background: var(--brand-orange); }
  .corner-tick--left { left: 0; }
  .corner-tick--right { right: 0; }
  .brand {
    position: absolute;
    top: 62px;
    right: 46px;
    display: flex;
    align-items: center;
    gap: 8px;
  }
  .brand-name {
    font-size: 34px;
    font-weight: 600;
    color: var(--brand-blue);
    letter-spacing: 0.5px;
  }
  .brand-mark {
    width: 9px;
    height: 9px;
    background: var(--brand-orange);
  }
  .center-tile {
    position: absolute;
    width: 112px;
    height: 112px;
    border-radius: 20px;
  }
  .center-tile--one { left: 150px; top: 230px; background: var(--tile-1); }
  .center-tile--two { left: 214px; top: 360px; background: var(--tile-2); }
  .center-tile--three { left: 278px; top: 490px; background: var(--tile-3); }
  .footer-band {
    position: absolute;
    left: 0;
    bottom: 6px;
    width: 540px;
    height: 150px;
    background: linear-gradient(to top, var(--footer-peach) 0%, rgba(245, 228, 213, 0.6) 45%, rgba(211, 225, 236, 0.25) 75%, rgba(247, 248, 249, 0) 100%);
  }
  .footer-rule {
    position: absolute;
    bottom: 0;
    height: 6px;
  }
  .footer-rule--orange { left: 0; width: 385px; background: var(--brand-orange); }
  .footer-rule--blue { left: 395px; width: 145px; background: var(--brand-blue); }
  .contact-line {
    position: absolute;
    left: 14px;
    bottom: 18px;
    display: flex;
    gap: 14px;
    font-size: 8.5px;
    color: var(--footer-text);
    white-space: nowrap;
  }
  .contact-item { display: flex; align-items: center; gap: 4px; }
  .contact-item svg { width: 8px; height: 8px; }
</style>
</head>
<body>
  <main class="letterhead">
    <div class="corner-tick corner-tick--left"><span class="tick-blue"></span><span class="tick-orange"></span></div>
    <div class="corner-tick corner-tick--right"><span class="tick-blue"></span><span class="tick-orange"></span></div>

    <header class="brand">
      <span class="brand-name">Zolvana</span>
      <span class="brand-mark"></span>
    </header>

    <div class="center-tile center-tile--one"></div>
    <div class="center-tile center-tile--two"></div>
    <div class="center-tile center-tile--three"></div>

    <div class="footer-band" role="img" aria-label="Soft peach and light blue wave ornament along the foot of the page"></div>
    <div class="footer-rule footer-rule--orange"></div>
    <div class="footer-rule footer-rule--blue"></div>

    <footer class="contact-line">
      <span class="contact-item">
        <svg viewBox="0 0 10 10"><circle cx="5" cy="5" r="5" fill="var(--brand-blue)"/><path d="M5 2a1.8 1.8 0 0 1 1.8 1.8C6.8 5.2 5 7.6 5 7.6S3.2 5.2 3.2 3.8A1.8 1.8 0 0 1 5 2z" fill="#fff"/></svg>
        Two Harbor Plaza 450 9th Avenue SE
      </span>
      <span class="contact-item">
        <svg viewBox="0 0 10 10"><circle cx="5" cy="5" r="5" fill="var(--brand-blue)"/><path d="M3.2 2.6l1 .1.5 1.3-.6.5a3.4 3.4 0 0 0 1.4 1.4l.5-.6 1.3.5.1 1c-2.2.6-4.8-2-4.2-4.2z" fill="#fff"/></svg>
        8005550142
      </span>
      <span class="contact-item">
        <svg viewBox="0 0 10 10"><circle cx="5" cy="5" r="5" fill="var(--brand-blue)"/><rect x="2.6" y="3.3" width="4.8" height="3.4" fill="#fff"/><path d="M2.6 3.3L5 5.2l2.4-1.9" stroke="var(--brand-blue)" stroke-width="0.5" fill="none"/></svg>
        info@zolvanaworks.example
      </span>
      <span class="contact-item">
        <svg viewBox="0 0 10 10"><circle cx="5" cy="5" r="5" fill="var(--brand-blue)"/><circle cx="5" cy="5" r="2.6" stroke="#fff" stroke-width="0.6" fill="none"/><path d="M2.4 5h5.2M5 2.4c-1.2 1.4-1.2 3.8 0 5.2M5 2.4c1.2 1.4 1.2 3.8 0 5.2" stroke="#fff" stroke-width="0.5" fill="none"/></svg>
        www.zolvanaworks.example
      </span>
    </footer>
  </main>
</body>
</html>
```